Business card for my new company (Accounting firm)

I need a business card for my new business Brightwell Advisory and Ledger SA. Our services are accounting, tax, audit and financial management. Our customers are small companies, start-ups and new companies. The final design has to show financial security, trust and growth. Please find our logo attached to the business card. Text for the business card: Brightwell Advisory and Ledger SA Tomas Varenholt Director and Founder Certified Accountant Tel. 022 418 57 34 tv@clairevalconseil.ch www.clairevalconseil.ch Rue des Vergières 27 1201 Geneva
Target Market(s)
Our customers are small companies, start-ups and new companies.
Industry/Entity Type
Finance And Accounting
Contact Information for Business Card
Claireval Conseil et Comptes SA
Tomas Varenholt
Directeur et Fondateur
Expert-comptable diplômé
Tél. 022 418 57 34
tv@clairevalconseil.ch
www.clairevalconseil.ch
Rue des Vergières 27
1201 Genève

```html
<!DOCTYPE html>
<html lang="fr">
<head>
<meta charset="utf-8">
<title>Claireval Conseil et Comptes SA – Carte de visite</title>
<link rel="stylesheet" href="https://fonts.googleapis.com/css2?family=Roboto:wght@400;500;700&display=swap">
<style>
  :root {
    --backdrop: #232122;
    --paper: #ffffff;
    --brand-blue: #1a6391;
    --accent-blue: #35aee3;
    --ink: #3d3d3d;
    --ink-soft: #4a4a4a;
  }
  * { margin: 0; padding: 0; box-sizing: border-box; }
  html, body {
    width: 1125px;
    height: 1200px;
    overflow: hidden;
    background: var(--backdrop);
    font-family: "Roboto", Arial, sans-serif;
  }
  .card {
    position: absolute;
    left: 171px;
    width: 826px;
    height: 472px;
  }
  .card--front { top: 106px; background: var(--paper); }
  .card--back { top: 639px; background: var(--brand-blue); }

  .title-band {
    position: absolute;
    left: 0;
    top: 62px;
    width: 671px;
    height: 126px;
    background: var(--brand-blue);
  }
  .holder-name {
    position: absolute;
    left: 41px;
    top: 22px;
    font-size: 30px;
    font-weight: 700;
    color: var(--accent-blue);
  }
  .holder-roles {
    position: absolute;
    left: 41px;
    top: 60px;
    font-size: 17.5px;
    line-height: 25px;
    color: var(--paper);
  }

  .brand {
    position: absolute;
    right: 52px;
    top: 192px;
    display: flex;
    align-items: center;
    gap: 12px;
  }
  .brand__square {
    width: 22px;
    height: 22px;
    background: var(--accent-blue);
  }
  .brand__name {
    font-size: 38px;
    font-weight: 500;
    letter-spacing: 2px;
    color: var(--ink);
  }

  .contact-list {
    position: absolute;
    left: 46px;
    top: 354px;
    list-style: none;
    font-size: 19px;
    line-height: 25px;
    color: var(--ink-soft);
  }
  .contact-list li { display: flex; align-items: center; gap: 8px; }
  .contact-list svg { width: 14px; height: 14px; fill: var(--accent-blue); }

  .address {
    position: absolute;
    right: 52px;
    top: 379px;
    text-align: right;
    font-style: normal;
    font-size: 19px;
    line-height: 25px;
    color: var(--ink-soft);
  }

  .back-brand {
    position: absolute;
    left: 0;
    right: 0;
    top: 170px;
    text-align: center;
    font-size: 56px;
    font-weight: 500;
    letter-spacing: 4px;
    color: var(--paper);
  }
  .back-url {
    position: absolute;
    left: 0;
    right: 0;
    top: 388px;
    text-align: center;
    font-size: 19px;
    letter-spacing: 4.5px;
    color: var(--paper);
  }
</style>
</head>
<body>
  <section class="card card--front">
    <div class="title-band">
      <h1 class="holder-name">Tomas Varenholt</h1>
      <p class="holder-roles">Directeur et Fondateur<br>Expert-comptable diplômé</p>
    </div>

    <div class="brand">
      <span class="brand__square"></span>
      <span class="brand__name">CLAIREVAL</span>
    </div>

    <ul class="contact-list">
      <li>
        <svg viewBox="0 0 16 16" aria-hidden="true"><path d="M3.6 1.2 5.8 1l1.2 3.3-1.5 1.2a8.5 8.5 0 0 0 5 5l1.2-1.5 3.3 1.2-.2 2.2c-.1.8-.8 1.4-1.6 1.4C6.6 13.8 2.2 9.4 2.2 2.8c0-.8.6-1.5 1.4-1.6z"/></svg>
        022 418 57 34
      </li>
      <li>
        <svg viewBox="0 0 16 16" aria-hidden="true"><path d="M1 3h14v1.2L8 8.6 1 4.2z"/><path d="M1 5.8l7 4.4 7-4.4V13H1z"/></svg>
        tv@clairevalconseil.ch
      </li>
      <li>
        <svg viewBox="0 0 16 16" aria-hidden="true"><circle cx="8" cy="8" r="7"/><path d="M4 5c1.5.3 2.5 1.4 2.2 2.8-.3 1.1 1 1.5 1 2.7 0 1-.6 2-.6 3.2" fill="none" stroke="#fff" stroke-width="1.2"/><path d="M10 2.5c-.3 1.2.6 2 1.6 2.2" fill="none" stroke="#fff" stroke-width="1.2"/></svg>
        www.clairevalconseil.ch
      </li>
    </ul>

    <address class="address">
      Rue des Vergières 27<br>1201 Genève
    </address>
  </section>

  <section class="card card--back">
    <p class="back-brand">CLAIREVAL</p>
    <p class="back-url">www.clairevalconseil.ch</p>
  </section>
</body>
</html>
```